wealth management firm, professional group, new model

we have a logo that works but we need a card, white background using our colors...clean look

our tag line if can be used in

The Bridge From Client to Owner

```html
<!DOCTYPE html>
<html lang="en">
<head>
<meta charset="UTF-8">
<title>Arvel Wealth Partners – Business Card</title>
<link href="https://fonts.googleapis.com/css2?family=Open+Sans:wght@400;600;700&display=swap" rel="stylesheet">
<style>
  :root {
    --navy: #1b3360;
    --ink: #3c3f46;
    --paper: #ffffff;
    --paper-shade: #f1f2f4;
    --rule: #c9ccd4;
    --arc-shadow: #d5d8de;
    --backdrop: #e4e5e8;
  }
  * { margin: 0; padding: 0; box-sizing: border-box; }
  html, body {
    width: 1200px; height: 900px; overflow: hidden;
    background: var(--backdrop);
    font-family: "Open Sans", Arial, sans-serif;
  }
  .stage {
    position: relative; width: 1200px; height: 900px;
    display: flex; justify-content: center; align-items: center; gap: 60px;
  }
  .card {
    position: relative; width: 300px; height: 525px;
    background: linear-gradient(180deg, var(--paper) 0%, var(--paper-shade) 100%);
    box-shadow: 0 6px 18px rgba(0,0,0,0.18);
    overflow: hidden;
  }
  .card-band { position: absolute; top: 0; left: 0; width: 300px; height: 110px; }

  .brand {
    position: absolute; left: 0; right: 0;
    display: flex; justify-content: center; align-items: center; gap: 8px;
    color: var(--navy); font-size: 20px; font-weight: 600; line-height: 1;
  }
  .brand-dot { width: 10px; height: 10px; border-radius: 50%; background: var(--navy); }
  .front .brand { top: 150px; }
  .back .brand { top: 380px; }

  .person { position: absolute; top: 222px; left: 0; right: 0; text-align: center; }
  .person-name { color: var(--navy); font-weight: 700; font-size: 16px; letter-spacing: 0.3px; line-height: 20px; }
  .person-role { color: var(--ink); font-size: 13px; line-height: 17px; }

  .divider {
    position: absolute; left: 28px; right: 28px; height: 1px;
    background: linear-gradient(90deg, transparent, var(--rule) 20%, var(--rule) 80%, transparent);
  }
  .icon-row {
    position: absolute; left: 0; right: 0; height: 20px;
    display: flex; justify-content: center; align-items: center; gap: 4px;
  }
  .icon-row::before, .icon-row::after {
    content: ""; width: 40px; height: 1px; background: var(--rule); margin: 0 4px;
  }
  .icon { width: 20px; height: 20px; display: block; }

  .details { position: absolute; left: 0; right: 0; text-align: center; color: var(--ink); font-size: 14px; line-height: 20px; }
  .address { top: 300px; }
  .phone { top: 396px; }
  .web { top: 432px; line-height: 22px; }
</style>
</head>
<body>
<main class="stage">
  <section class="card front" aria-label="Card front">
    <svg class="card-band" viewBox="0 0 300 110" aria-hidden="true">
      <path d="M0 0 H300 V26 Q140 26 0 100 Z" fill="var(--navy)"/>
      <path d="M300 26 Q140 26 0 100" fill="none" stroke="var(--arc-shadow)" stroke-width="4" transform="translate(0,3)"/>
    </svg>

    <div class="brand"><span class="brand-dot"></span>Arvel Wealth Partners</div>

    <div class="person">
      <div class="person-name">DANIEL REED</div>
      <div class="person-role">Director</div>
    </div>

    <div class="divider" style="top:266px"></div>

    <div class="icon-row" style="top:276px">
      <svg class="icon" viewBox="0 0 20 20" aria-label="Address">
        <circle cx="10" cy="10" r="10" fill="var(--navy)"/>
        <path d="M10 4.5a3.6 3.6 0 0 0-3.6 3.6c0 2.7 3.6 6.9 3.6 6.9s3.6-4.2 3.6-6.9A3.6 3.6 0 0 0 10 4.5z" fill="#fff"/>
        <circle cx="10" cy="8.1" r="1.4" fill="var(--navy)"/>
      </svg>
    </div>
    <div class="details address">00 dummy city<br>dummy place 0000</div>

    <div class="divider" style="top:352px"></div>

    <div class="icon-row" style="top:368px">
      <svg class="icon" viewBox="0 0 20 20" aria-label="Phone">
        <circle cx="10" cy="10" r="10" fill="var(--navy)"/>
        <path d="M7 5.5l1.6 2.4-1 1a6 6 0 0 0 2.9 2.9l1-1 2.4 1.6-.8 1.7c-3.8.2-7.9-3.9-7.7-7.7z" fill="#fff"/>
      </svg>
      <svg class="icon" viewBox="0 0 20 20" aria-label="Email">
        <circle cx="10" cy="10" r="10" fill="var(--navy)"/>
        <rect x="5" y="6.5" width="10" height="7" fill="#fff"/>
        <path d="M5 6.5l5 4 5-4" fill="none" stroke="var(--navy)" stroke-width="1"/>
      </svg>
      <svg class="icon" viewBox="0 0 20 20" aria-label="Website">
        <circle cx="10" cy="10" r="10" fill="var(--navy)"/>
        <g fill="none" stroke="#fff" stroke-width="1">
          <circle cx="10" cy="10" r="5.2"/>
          <ellipse cx="10" cy="10" rx="2.2" ry="5.2"/>
          <path d="M4.8 10h10.4M5.6 7.4h8.8M5.6 12.6h8.8"/>
        </g>
      </svg>
    </div>
    <div class="details phone">555-200-9000</div>

    <div class="divider" style="top:424px"></div>

    <div class="details web">info@arvelwealth.com<br>www.arvelwealth.com</div>
  </section>

  <section class="card back" aria-label="Card back">
    <div class="brand"><span class="brand-dot"></span>Arvel Wealth Partners</div>
  </section>
</main>
</body>
</html>
```